Honey Company from Florida Needs Sweet and Buzz-worthy Site

Website Requests:
-Deluxe 5-Page Website with SSL-Secure Online Store (Shopify)
-High-end imagery to appeal to a discerning consumer
-Detailed verbiage with strong SEO and easy readability
-Design principles: simple, chic, luxe, earthy
Pages:
1. Home {Local, Raw American Honey from Florida}
2. The Hive
> About Us
>Meet the Beekeepers
3. Buy Honey
> Shopify retail store
4. The Buzz {News, Recipes & More}
> Blog
5. Contact Us {We're Buzzin' to Meet You}
> Store Hours
> Phone Number
> Address
> Quick Contact Form
Attachments: Web design notes, Logo, Color Codes, Inspiration Photos
Target Market(s)
High-end honey consumer in the U.S.
Industry/Entity Type
Upscale honey enthusiasts; direct to consumer sales.
Coding
Coded - Design and coding required
Number of Pages Required
5+ page
Requirements
Must have
- Upscale look and feel, easy usability for quick sales.

```html
<!DOCTYPE html>
<html lang="en">
<head>
<meta charset="utf-8">
<title>Golden Comb Honey Co.</title>
<link rel="stylesheet" href="https://fonts.googleapis.com/css2?family=Roboto+Slab:wght@400;500;700;800&family=Noto+Serif:wght@400&display=swap">
<style>
:root{
  --gold:#ecc350;
  --gold-title:#e6bd55;
  --ink:#1f1d1a;
  --text:#3d3a35;
  --white:#ffffff;
  --line:#d9b547;
}
*{box-sizing:border-box;margin:0;padding:0}
html,body{width:1200px;height:3844px;overflow:hidden;background:var(--white)}
body{position:relative;font-family:"Noto Serif",Georgia,serif;color:var(--text)}

/* header */
.site-header{position:absolute;left:0;top:0;width:1200px;height:233px}
.round-btn{position:absolute;width:70px;height:70px;border:2px solid var(--gold);border-radius:50%;display:flex;align-items:center;justify-content:center;background:var(--white)}
.menu-btn{left:115px;top:44px}
.cart-btn{left:1046px;top:44px;flex-direction:column}
.cart-count{font-family:"Roboto Slab",serif;font-size:15px;color:var(--gold);line-height:1;margin-bottom:2px}
.nav-band{position:absolute;left:0;top:160px;width:1200px;height:73px;background:var(--gold)}
.nav-link{position:absolute;top:185px;font-family:"Roboto Slab",serif;font-weight:700;font-size:16px;color:var(--ink);text-decoration:none;letter-spacing:.2px;white-space:nowrap}
.brand-badge{position:absolute;left:520px;top:-8px;width:180px;height:220px;border-radius:0 0 90px 90px;background:var(--white)}
.brand-ring{position:absolute;left:536px;top:20px;width:160px;height:160px;border-radius:50%;border:3px solid var(--ink);background:var(--white)}
.brand-name{position:absolute;left:536px;top:20px;width:160px;height:160px;display:flex;align-items:center;justify-content:center;text-align:center;font-family:"Roboto Slab",serif;font-weight:700;font-size:24px;line-height:1.1;color:var(--ink)}

/* hero */
.hero{position:absolute;left:0;top:233px;width:1200px;height:676px;background:radial-gradient(ellipse at 35% 55%,#f3a83a 0%,#e9962a 35%,#d98a2a 60%,#f0b85a 100%)}
.hero-title{position:absolute;left:655px;top:468px;width:500px;text-align:center;white-space:nowrap;font-family:"Roboto Slab",serif;font-weight:800;font-size:58px;line-height:70px;color:var(--white);letter-spacing:1px}
.hero-sub{position:absolute;left:655px;top:562px;width:500px;text-align:center;white-space:nowrap;font-size:16px;color:var(--white)}
.hero-btn{position:absolute;left:828px;top:604px;width:170px;height:57px;border:2px solid var(--white);border-radius:4px;display:flex;align-items:center;justify-content:center;gap:10px;font-family:"Roboto Slab",serif;font-weight:700;font-size:16px;color:var(--white);white-space:nowrap}

/* shared */
.section-mark{position:absolute;width:44px;height:30px;border-radius:15px;background:#2a2622}
.section-title{position:absolute;left:0;width:1200px;text-align:center;white-space:nowrap;font-family:"Roboto Slab",serif;font-weight:700;color:var(--gold-title);letter-spacing:1px}

/* intro */
.intro-copy{position:absolute;left:236px;top:1070px;width:758px;text-align:center;font-size:14px;line-height:32.6px;color:var(--text)}

/* feature rows */
.photo{position:absolute}
.panel{position:absolute;background:var(--gold)}
.feature-title{position:absolute;white-space:nowrap;font-family:"Roboto Slab",serif;font-weight:700;font-size:25px;color:var(--ink);letter-spacing:.3px}
.feature-sub{position:absolute;white-space:nowrap;font-family:"Roboto Slab",serif;font-weight:400;font-size:26px;color:var(--ink)}
.feature-copy{position:absolute;font-size:14px;line-height:28px;color:var(--ink);text-align:justify}
.outline-btn{position:absolute;height:49px;border:2px solid var(--ink);border-radius:4px;display:flex;align-items:center;justify-content:center;font-family:"Roboto Slab",serif;font-size:15px;color:var(--ink);white-space:nowrap}

/* blog */
.post-title{position:absolute;left:0;top:2814px;width:1200px;text-align:center;font-family:"Roboto Slab",serif;font-weight:700;font-size:23px;color:var(--ink);letter-spacing:.3px}
.post-date{position:absolute;left:0;top:2862px;width:1200px;text-align:center;font-family:"Roboto Slab",serif;font-weight:500;font-size:22px;color:var(--gold-title);letter-spacing:1px}
.post-copy{position:absolute;left:300px;top:2903px;width:600px;text-align:center;font-size:14px;line-height:29.5px;color:var(--text)}

/* gallery */
.gallery-tile{position:absolute;top:3084px;height:256px}

/* signup */
.signup{position:absolute;left:0;top:3340px;width:1200px;height:328px;background:var(--gold)}
.signup-title{position:absolute;left:0;top:3393px;width:1200px;text-align:center;font-family:"Roboto Slab",serif;font-weight:700;font-size:33px;color:var(--ink);letter-spacing:.5px}
.signup-sub{position:absolute;left:0;top:3446px;width:1200px;text-align:center;font-family:"Roboto Slab",serif;font-size:20px;color:var(--ink)}
.email-field{position:absolute;left:236px;top:3492px;width:758px;height:56px;border:1.5px solid #8a7232;border-radius:4px;padding-left:16px;display:flex;align-items:center;font-size:15px;color:var(--ink)}
.submit-btn{position:absolute;left:530px;top:3567px;width:170px;height:56px;border-radius:4px;background:var(--ink);color:var(--white);display:flex;align-items:center;justify-content:center;font-family:"Roboto Slab",serif;font-weight:700;font-size:18px;letter-spacing:.5px}

/* footer */
.footer-contact{position:absolute;left:0;top:3722px;width:1200px;text-align:center;font-family:"Roboto Slab",serif;font-size:19px;color:var(--ink)}
.footer-contact .sep{margin:0 22px}
.footer-legal{position:absolute;left:0;top:3773px;width:1200px;text-align:center;font-size:14px;color:var(--ink)}
</style>
</head>
<body>

<header class="site-header">
  <div class="round-btn menu-btn" aria-label="Menu">
    <svg width="20" height="16" viewBox="0 0 20 16"><rect y="0" width="20" height="3" fill="#ecc350"/><rect y="6.5" width="20" height="3" fill="#ecc350"/><rect y="13" width="20" height="3" fill="#ecc350"/></svg>
  </div>
  <div class="round-btn cart-btn" aria-label="Cart">
    <span class="cart-count">0</span>
    <svg width="20" height="17" viewBox="0 0 20 17"><path d="M0 1h3.5l2.5 9h11l2-7H5" fill="none" stroke="#ecc350" stroke-width="2.4"/><circle cx="7.5" cy="14.5" r="2" fill="#ecc350"/><circle cx="15.5" cy="14.5" r="2" fill="#ecc350"/></svg>
  </div>
  <div class="nav-band"></div>
  <nav>
    <a class="nav-link" style="left:164px" href="#">HOME</a>
    <a class="nav-link" style="left:266px" href="#">THE HIVE</a>
    <a class="nav-link" style="left:394px" href="#">BUY HONEY</a>
    <a class="nav-link" style="left:749px" href="#">THE BUZZ</a>
    <a class="nav-link" style="left:881px" href="#">CONTACT</a>
  </nav>
  <div class="brand-badge"></div>
  <div class="brand-ring"></div>
  <div class="brand-name">Golden<br>Comb<br>Honey Co.</div>
</header>

<section class="hero" role="img" aria-label="Photo of a jar of honey with a dipper, dripping honey, honeycomb background and daisies"></section>
<h1 class="hero-title">GOLDENCOMB</h1>
<p class="hero-sub">SED UT PERSPICIATIS UNDE OMNIS ISTE NATUS ERROR</p>
<div class="hero-btn">PLAY VIDEO
  <svg width="20" height="20" viewBox="0 0 20 20"><circle cx="10" cy="10" r="8" fill="none" stroke="#fff" stroke-width="2"/><path d="M8 6l6 4-6 4z" fill="#fff"/></svg>
</div>

<section class="intro">
  <div class="section-mark" role="img" aria-label="Small bee emblem" style="left:578px;top:952px"></div>
  <h2 class="section-title" style="top:990px;font-size:44px">GOES HERE</h2>
  <p class="intro-copy">100% raw, unfiltered Florida honey straight from he beehives on his six-acre property, Golden Comb Honey Farm, 1480 Orchard Lane in Marigold. Agricultural Company specializing in the Production of 100% Raw American Honey, and the Pollination of America's food crops. Our Honey comes straight from our beehives to your table. No filtering, heating, or any funny stuff. Just All Natural, 100% Pure Florida Honey Natural Wild Honey- flavors include Orange Blossom, Gallberry, Summer Wildflower, Winter Wildflower, and many more. Bee Pollen, Royal Jelly, and Bee venom. Bee removals are done by Walter Hensley, owner of Golden Comb Honey Farm, has about 1,200 beehives that he moves around to pollinate different plants.</p>
</section>

<section class="feature">
  <div class="photo" role="img" aria-label="Photo of a wooden gift box with a honey jar, tea leaves and cinnamon sticks" style="left:0;top:1373px;width:615px;height:433px;background:linear-gradient(135deg,#b8b2a6,#8d867b 55%,#a88a6a)"></div>
  <div class="panel" style="left:615px;top:1373px;width:585px;height:433px"></div>
  <h3 class="feature-title" style="left:670px;top:1436px">IMPORTANCE OF BEES</h3>
  <p class="feature-sub" style="left:670px;top:1473px">Don’t Judge a Bee by Its Stinger</p>
  <p class="feature-copy" style="left:670px;top:1531px;width:443px">If the bee disappeared off the face of the Earth, man would have only four years left to live. Hyper-efficient insects do play a vital role agriculture. Almonds, for example almost entirely dependent on honeybee pollination.Over one-third of our entire diet is dependent on pollination from the honeybee.</p>
  <div class="outline-btn" style="left:675px;top:1698px;width:137px">READ MORE</div>

  <div class="panel" style="left:0;top:1806px;width:615px;height:431px"></div>
  <h3 class="feature-title" style="left:113px;top:1869px">THE HEALTH BENEFITS OF HONEY</h3>
  <p class="feature-sub" style="left:113px;top:1906px">Real Local Honey, Really Good for You</p>
  <p class="feature-copy" style="left:115px;top:1964px;width:444px;text-align:left">Raw honey is loaded with antioxidants to protect your body from cell damage due to free radicals. Honey has been long known as a folk remedy to help heal burns and wounds due to its antibacterial and antifungal properties. Honey is also very well known to soothe a sore throat. Try taking a spoonful of honey</p>
  <div class="outline-btn" style="left:118px;top:2131px;width:137px">READ MORE</div>
  <div class="photo" role="img" aria-label="Photo of a honey jar with a wooden dipper among herbs and chamomile flowers" style="left:615px;top:1806px;width:585px;height:431px;background:linear-gradient(135deg,#3c4a2a,#6b5a33 45%,#c9902f 70%,#5a4a2c)"></div>
</section>

<section class="blog">
  <div class="section-mark" role="img" aria-label="Small bee emblem" style="left:578px;top:2280px"></div>
  <h2 class="section-title" style="top:2318px;font-size:44px">LATEST BLOG POST</h2>
  <div class="photo" role="img" aria-label="Blog photo of honeycomb, honey dippers and yellow flowers around the company name" style="left:261px;top:2403px;width:709px;height:383px;background:radial-gradient(ellipse at center,#fbf6ea 0%,#f7eccd 45%,#f0c860 100%);border:1px solid #e8e1cf"></div>
  <h3 class="post-title">SED UT PERSPICIATIS UNDE OMNIS</h3>
  <p class="post-date">OCT 04, 2021</p>
  <p class="post-copy">Nemo enim ipsam voluptatem quia voluptas sit aspernatur aut odit aut fugit, sed quia consequuntur magni dolores eos qui ratione voluptatem sequi nesciunt. Neque porro quisquam est, qui dolorem ipsum quia dolor sit amet, consectetur, adipisci velit, sed incidunt ut labore et dolore magnam aliquam quaerat voluptatem.</p>
</section>

<section class="gallery">
  <div class="gallery-tile" role="img" aria-label="Photo of a honey dipper over a bowl of honey" style="left:0;width:239px;background:linear-gradient(135deg,#f2d9a8,#e49a25 55%,#8a4d16)"></div>
  <div class="gallery-tile" role="img" aria-label="Photo of honey jars with nuts and a dipper" style="left:246px;width:240px;background:linear-gradient(135deg,#5a4634,#b07a33 55%,#6c5038)"></div>
  <div class="gallery-tile" role="img" aria-label="Photo of honey pouring from a spoon into a jar" style="left:494px;width:240px;background:linear-gradient(135deg,#6a5948,#d99b32 55%,#7d6a57)"></div>
  <div class="gallery-tile" role="img" aria-label="Photo of a covered honey jar with a wooden dipper" style="left:742px;width:240px;background:linear-gradient(135deg,#8f8880,#b58a49 55%,#7b726a)"></div>
  <div class="gallery-tile" role="img" aria-label="Photo of a honey jar beside a piece of honeycomb" style="left:990px;width:210px;background:linear-gradient(135deg,#d8d2c6,#f0b035 55%,#c9c1b3)"></div>
</section>

<section class="signup"></section>
<h2 class="signup-title">SIGN-UP FOR OUR EMAILS</h2>
<p class="signup-sub">Sed ut perspiciatis unde omnis iste natus error sit voluptatem accusantium</p>
<div class="email-field">Enter Your Email :</div>
<div class="submit-btn">SUBMIT</div>

<footer>
  <p class="footer-contact">(555) 014-2278<span class="sep">|</span>1480 Orchard Lane, Marigold, FL 34000</p>
  <p class="footer-legal">© Copyright 2021 Golden Comb.All Rights Reserved</p>
</footer>

</body>
</html>
```